Kirvo Store Banner

I have an kirvo store which displays the store name which is Mrs.Brindle's Humming Garden-Shop. I want to make this store landing page look better so I want a design to be used as what kirvo calls a Store banner. I attach a pic of the visuals of the landing page of my store and I also attach a pic of another store who have set up a banner.

Colors
85cae6
6cbee2
33a6d7
0355a3
3276b5
cedeed
d6edf3
eaf1f7

```html
<!DOCTYPE html>
<html lang="en">
<head>
<meta charset="utf-8">
<title>Kirvo Store Banner – Mrs.Brindle's Humming Garden-Shop</title>
<link rel="stylesheet" href="https://fonts.googleapis.com/css2?family=Rubik:wght@700&display=swap">
<style>
  :root {
    --page: #ffffff;
    --sky-100: #eaf1f7;
    --sky-200: #d6edf3;
    --sky-300: #cedeed;
    --sky-400: #85cae6;
    --sky-500: #6cbee2;
    --sky-600: #33a6d7;
    --blue-700: #3276b5;
    --blue-800: #0355a3;
    --frame-grey: #b0b0b0;
  }
  html, body {
    margin: 0;
    padding: 0;
    width: 1200px;
    height: 459px;
    overflow: hidden;
    background: var(--page);
  }
  .canvas {
    position: relative;
    width: 1200px;
    height: 459px;
  }
  .store-banner {
    position: absolute;
    left: 86px;
    top: 82px;
    width: 1028px;
    height: 232px;
    background: var(--page);
    box-shadow: 0 4px 14px rgba(0, 0, 0, 0.18);
    overflow: hidden;
  }
  .store-banner svg {
    display: block;
    width: 100%;
    height: 100%;
  }
  .ring { fill: none; stroke-width: 15; }
  .ring--deep { stroke: var(--blue-800); }
  .ring--bright { stroke: var(--sky-600); }
  .store-badge {
    position: absolute;
    left: 140px;
    top: 249px;
    width: 121px;
    height: 121px;
    background: var(--page);
    border: 3px solid var(--frame-grey);
    display: flex;
    align-items: center;
    justify-content: center;
    text-align: center;
  }
  .store-badge__name {
    margin: 0;
    padding: 0 8px;
    font-family: "Rubik", sans-serif;
    font-weight: 700;
    font-size: 13px;
    line-height: 1.2;
    color: var(--blue-800);
  }
</style>
</head>
<body>
<div class="canvas">
  <div class="store-banner">
    <svg viewBox="0 0 1200 270" preserveAspectRatio="none" xmlns="http://www.w3.org/2000/svg">
      <defs>
        <radialGradient id="tone-mint" cx="50%" cy="50%" r="60%"><stop offset="0" stop-color="#cfe9cf"/><stop offset="1" stop-color="#eef3ee"/></radialGradient>
        <radialGradient id="tone-wood" cx="50%" cy="50%" r="60%"><stop offset="0" stop-color="#9b4a2a"/><stop offset="1" stop-color="#f2eeea"/></radialGradient>
        <radialGradient id="tone-bowl" cx="50%" cy="60%" r="60%"><stop offset="0" stop-color="#2a211c"/><stop offset="1" stop-color="#c8c4c0"/></radialGradient>
        <radialGradient id="tone-glass-dark" cx="50%" cy="50%" r="60%"><stop offset="0" stop-color="#6a6e72"/><stop offset="1" stop-color="#101114"/></radialGradient>
        <radialGradient id="tone-record" cx="50%" cy="50%" r="60%"><stop offset="0" stop-color="#c8642a"/><stop offset="1" stop-color="#e6b24a"/></radialGradient>
        <radialGradient id="tone-bottle" cx="50%" cy="50%" r="60%"><stop offset="0" stop-color="#c9c4bd"/><stop offset="1" stop-color="#8c8580"/></radialGradient>
        <radialGradient id="tone-shade" cx="50%" cy="50%" r="60%"><stop offset="0" stop-color="#ece6d8"/><stop offset="1" stop-color="#4a3a34"/></radialGradient>
        <radialGradient id="tone-amber" cx="50%" cy="50%" r="60%"><stop offset="0" stop-color="#e79a3a"/><stop offset="1" stop-color="#f0ece4"/></radialGradient>
        <radialGradient id="tone-navy" cx="50%" cy="50%" r="60%"><stop offset="0" stop-color="#aab4c0"/><stop offset="1" stop-color="#1f2c44"/></radialGradient>
      </defs>

      <circle class="ring ring--deep" cx="75" cy="-2" r="95"/>
      <g role="img" aria-label="Photo of a green glass vase with gold bands"><circle cx="90" cy="-8" r="82" fill="url(#tone-mint)"/></g>

      <circle class="ring ring--deep" cx="60" cy="178" r="112"/>
      <g role="img" aria-label="Photo of two boxed collectible items in red packaging"><circle cx="45" cy="178" r="105" fill="url(#tone-wood)"/></g>

      <circle class="ring ring--bright" cx="280" cy="10" r="100"/>
      <g role="img" aria-label="Photo of a dark brown ceramic bowl"><circle cx="283" cy="14" r="88" fill="url(#tone-bowl)"/></g>

      <circle class="ring ring--bright" cx="282" cy="204" r="100"/>
      <g role="img" aria-label="Photo of three clear glass footed mugs"><circle cx="258" cy="218" r="88" fill="url(#tone-glass-dark)"/></g>

      <circle class="ring ring--deep" cx="476" cy="110" r="100"/>
      <g role="img" aria-label="Photo of two vintage record sleeves"><circle cx="468" cy="104" r="88" fill="url(#tone-record)"/></g>

      <circle class="ring ring--deep" cx="660" cy="28" r="100"/>
      <g role="img" aria-label="Photo of a row of textured glass tumblers"><circle cx="657" cy="24" r="88" fill="url(#tone-glass-dark)"/></g>

      <circle class="ring ring--deep" cx="672" cy="214" r="100"/>
      <g role="img" aria-label="Photo of a textured glass bottle with a cork stopper"><circle cx="666" cy="208" r="88" fill="url(#tone-bottle)"/></g>

      <circle class="ring ring--bright" cx="852" cy="110" r="100"/>
      <g role="img" aria-label="Photo of a tiered cream glass lamp shade"><circle cx="847" cy="128" r="88" fill="url(#tone-shade)"/></g>

      <circle class="ring ring--bright" cx="985" cy="272" r="100"/>
      <g role="img" aria-label="Photo of a tiered amber glass vase"><circle cx="1004" cy="290" r="88" fill="url(#tone-amber)"/></g>

      <circle class="ring ring--deep" cx="1060" cy="78" r="100"/>
      <g role="img" aria-label="Photo of a green glass jug with gold stripes"><circle cx="1042" cy="82" r="88" fill="url(#tone-mint)"/></g>

      <circle class="ring ring--deep" cx="1195" cy="232" r="100"/>
      <g role="img" aria-label="Photo of a textured clear glass jug"><circle cx="1205" cy="228" r="88" fill="url(#tone-navy)"/></g>
    </svg>
  </div>

  <div class="store-badge">
    <p class="store-badge__name">Mrs.Brindle's Humming Garden-Shop</p>
  </div>
</div>
</body>
</html>
```